Public Relations Agency Seeks Wordpress Design and Coding

TRELVOX Studio is a public relations agency specializing in media relations, public affairs and marketing communication.

The site should display the following visual characteristics: professionalism, trustworthiness, high-tech focus, clear and concise design.

The desired colors are royal blue, gray and hints of red.

Design look/feel inspired by this site: http://brightpathgatherings.example/

Specifications:

1. Navigation/Pages/Index:

HOME

ABOUT US

SERVICES

NEWS

CONTACT

---

2. Functionality of/content for each page:

- Home
o Dominant photo (professional, edgy, innovative)
o Simple, straightforward access to/from “Home” from other pages
o Includes logo (attached) and tagline "Unleash the power of communication"
o Direct link to “CONTACT”
o Links to social media accounts: Facebook, Twitter, LinkedIn

- About Us

o Company profile blurb
o President’s photo with short bio

- Services
o Public Relations
 Strategic communication
 Brand and reputation management
 Community relations
o Media Relations
 News coverage and contacts
 Media training and interview skills
 Crisis communications
o Congressional Affairs
 Public affairs
 Public policy
 Legislative strategy
o Mass Communication
 Speechwriting
 Presentation creation
 Social media
o Marketing Communications
 Business collateral material
 Promotional campaigns
 Special events and tradeshows

- News
o Blog-like page to post information and/or share news from other sites

- Contact
o Standard “Contact Us” form (Name, Email, Phone, Message)
o Direct Contact
 (407) 555-0164
 Marisol@TRELVOXstudio.example

Target Market(s)

Small to large businesses specializing in high technology, defense/military, medicine/healthcare, and wide array of professional services.

Industry/Entity Type

Marketing

Font styles to use
Serif
Sans Serif

Colors
0555a3
ec2027
edf3f7

Requirements
Must have
• -- Project reqires DESIGN - and - fully CODED.

-- Strong SEO

-- Optimized for mobile viewing

Thank you!

```html
<!DOCTYPE html>
<html lang="en">
<head>
<meta charset="utf-8">
<title>TRELVOX Studio – Public Relations Agency</title>
<link href="https://fonts.googleapis.com/css2?family=Oswald:wght@400;500;600&family=Open+Sans:wght@400;600;700&display=swap" rel="stylesheet">
<style>
:root{
  --red:#e3001b;
  --red-dark:#b3001a;
  --red-footer:#9a0015;
  --blue:#0d3c8f;
  --blue-btn:#0a3f8c;
  --gray-bg:#efefef;
  --white:#ffffff;
  --ink:#1c1c1c;
  --muted:#555555;
  --dark:#2b2b2b;
}
*{box-sizing:border-box;margin:0;padding:0}
html,body{width:1200px;height:3774px;overflow:hidden}
body{position:relative;background:var(--white);font-family:"Open Sans",Arial,sans-serif;color:var(--ink)}
section,header,footer,nav{position:absolute;left:0;width:1200px}

/* hero */
.hero{top:0;height:536px;background:linear-gradient(180deg,#6f6f6f 0%,#3d3d3d 45%,#545454 75%,#2a2a2a 100%);overflow:hidden}
.hero-figure{position:absolute;left:70px;top:0;width:240px;height:536px;background:linear-gradient(180deg,#8a8a8a,#1e1e1e)}
.hero-logo{position:absolute;top:40px;left:0;width:1200px;text-align:center;font-family:"Oswald",sans-serif;font-weight:600;font-size:58px;color:#5a5a5a;letter-spacing:2px;line-height:1}
.hero-logo span{display:block;font-size:20px;letter-spacing:10px;color:#5a5a5a;margin-top:2px}
.hero-title{position:absolute;top:168px;width:1200px;text-align:center;font-family:"Oswald",sans-serif;font-weight:500;font-size:150px;color:#fff;line-height:1;letter-spacing:1px}
.hero-sub{position:absolute;top:333px;width:1200px;text-align:center;font-family:"Oswald",sans-serif;font-weight:500;font-size:40px;color:#fff}
.btn{display:inline-block;background:var(--blue-btn);color:#fff;font-family:"Oswald",sans-serif;font-size:14px;text-transform:uppercase;text-align:center;border-radius:2px}
.hero .btn{position:absolute;left:536px;top:403px;width:126px;height:50px;line-height:50px}
.dots{position:absolute;top:499px;left:578px;display:flex;gap:10px}
.dots i{width:8px;height:8px;border-radius:50%;background:#9a9a9a}
.dots i.on{background:#e0e0e0}
.social{position:absolute;right:0;top:106px;width:63px;height:209px;background:var(--red);display:flex;flex-direction:column;align-items:center;justify-content:space-around;padding:14px 0}
.social a{width:34px;height:34px;border:2px solid #fff;border-radius:50%;display:block}

/* nav */
.topnav{top:536px;height:85px;background:var(--red)}
.brand{position:absolute;left:83px;top:12px;font-family:"Oswald",sans-serif;font-weight:600;font-size:44px;color:#fff;line-height:1;letter-spacing:1px}
.brand span{display:block;font-size:16px;letter-spacing:8px;text-align:center;margin-top:2px}
.menu{position:absolute;left:654px;top:0;display:flex;height:85px;list-style:none}
.menu li{font-family:"Oswald",sans-serif;font-size:15px;color:#fff;text-transform:uppercase;line-height:85px;padding:0 24px}
.menu li.active{background:var(--red-dark)}

/* intro */
.intro{top:621px;height:134px;display:flex;align-items:center;justify-content:center}
.intro h1{font-family:"Oswald",sans-serif;font-weight:500;font-size:23px;line-height:32px;text-transform:uppercase;text-align:center;width:900px}

/* services */
.services{top:755px;height:604px;background:var(--gray-bg)}
.section-title{font-family:"Oswald",sans-serif;font-weight:500;font-size:26px;text-transform:uppercase;text-align:center;position:absolute;width:1200px}
.services .section-title{top:40px}
.service-card{position:absolute;top:113px;width:232px;height:422px;background:#fff;text-align:center;padding:40px 22px 0}
.service-card h3{font-family:"Oswald",sans-serif;font-weight:400;font-size:16px;line-height:20px;text-transform:uppercase;margin-bottom:20px}
.service-card svg{display:block;margin:0 auto 26px}
.service-card p{font-size:12px;line-height:21px;color:var(--muted)}
.service-card.featured{background:var(--blue)}
.service-card.featured h3,.service-card.featured p{color:#fff}

/* cta */
.cta{top:1359px;height:206px}
.cta h2{position:absolute;top:40px;width:1200px;text-align:center;font-family:"Oswald",sans-serif;font-weight:500;font-size:22px;text-transform:uppercase}
.cta .btn{position:absolute;left:521px;top:93px;width:158px;height:58px;line-height:58px;font-size:15px}

/* agency band */
.agency{top:1565px;height:322px;background:linear-gradient(90deg,#1c1c1c,#4a4a4a 35%,#2d2d2d 65%,#575757)}
.agency h2{position:absolute;top:128px;width:1200px;text-align:center;font-family:"Oswald",sans-serif;font-weight:500;font-size:37px;color:#fff;text-transform:uppercase}
.agency p{position:absolute;top:183px;width:1200px;text-align:center;font-size:13px;color:#e8e8e8}

/* team */
.team{top:1887px;height:483px;background:var(--gray-bg)}
.team .section-title{top:50px;font-size:22px}
.team .lede{position:absolute;top:102px;width:1200px;text-align:center;font-size:14px;text-transform:uppercase;color:#333}
.member{position:absolute;top:176px;width:215px;height:215px;border-radius:50%;display:flex;align-items:center;justify-content:center}
.member-name{font-family:"Oswald",sans-serif;font-weight:500;font-size:17px;color:#fff;text-transform:uppercase}

/* testimonials */
.testimonials{top:2370px;height:322px;background:linear-gradient(90deg,#3a3a3a,#6b6b6b 40%,#2f2f2f 70%,#555)}
.testimonials h2{position:absolute;top:44px;width:1200px;text-align:center;font-family:"Oswald",sans-serif;font-weight:500;font-size:34px;color:#fff;text-transform:uppercase}
.quote-mark{position:absolute;top:104px;left:584px}
.testimonials p{position:absolute;top:158px;left:95px;width:1010px;text-align:center;font-size:13px;line-height:22px;color:#fff}
.testimonials cite{position:absolute;top:232px;width:1200px;text-align:center;font-size:14px;font-weight:700;font-style:italic;color:#fff}

/* clients */
.clients{top:2692px;height:252px}
.clients .section-title{top:65px;font-size:22px}
.client-row{position:absolute;top:145px;left:90px;width:1030px;display:flex;justify-content:space-between;align-items:center}
.client-row span{font-family:"Open Sans",sans-serif;font-weight:700;font-size:15px;color:#4a4a4a}

/* news */
.news{top:2944px;height:339px;background:var(--gray-bg)}
.news .section-title{top:32px;font-size:22px}
.news-arrows{position:absolute;top:42px;left:1080px;display:flex;gap:18px}
.news-tile{position:absolute;top:105px;width:292px;height:177px}
.news-card{background:#2f2f2f;color:#fff;padding:24px 26px}
.news-card h3{font-family:"Open Sans",sans-serif;font-weight:700;font-size:15px;text-transform:uppercase}
.news-card time{display:block;font-size:11px;margin:4px 0 12px}
.news-card p{font-size:11px;line-height:15px;color:#dcdcdc}

/* contact */
.contact{top:3283px;height:398px;background:var(--red)}
.contact h2{position:absolute;top:40px;left:86px;font-family:"Oswald",sans-serif;font-weight:500;font-size:22px;color:#fff;text-transform:uppercase}
.field{position:absolute;background:#fff;font-size:11px;color:#555;padding:16px 12px;text-transform:uppercase}
.submit{position:absolute;left:86px;top:315px;width:103px;height:55px;background:#5a0010;color:#fff;font-family:"Oswald",sans-serif;font-size:14px;line-height:55px;text-align:center;text-transform:uppercase}
.info{position:absolute;left:680px;width:470px;display:flex;gap:16px;color:#fff;font-size:13px;line-height:20px}
.info svg{flex:none;margin-top:2px}

/* footer */
.site-footer{top:3681px;height:93px;background:var(--red-footer);color:#fff;font-size:12px;text-align:center;line-height:93px}
</style>
</head>
<body>

<header class="hero">
  <div class="hero-figure" role="img" aria-label="Photo of a businessman in a dark suit standing under a cloudy sky"></div>
  <div class="hero-logo">TRELVOX<span>STUDIO</span></div>
  <div class="hero-title">UNLEASH</div>
  <div class="hero-sub">THE POWER OF COMMUNICATION</div>
  <a class="btn">Read More</a>
  <div class="dots"><i></i><i class="on"></i><i></i></div>
  <div class="social">
    <a aria-label="Facebook"></a>
    <a aria-label="Twitter"></a>
    <a aria-label="LinkedIn"></a>
  </div>
</header>

<nav class="topnav">
  <div class="brand">TRELVOX<span>STUDIO</span></div>
  <ul class="menu">
    <li class="active">Home</li>
    <li>About Us</li>
    <li>Services</li>
    <li>News</li>
    <li>Contact Us</li>
  </ul>
</nav>

<section class="intro">
  <h1>TRELVOX Studio are public relations agency specializing in media relations, public affairs and marketing communication</h1>
</section>

<section class="services">
  <h2 class="section-title">Our Services</h2>

  <article class="service-card featured" style="left:86px">
    <h3>Public Relations</h3>
    <svg width="118" height="118" viewBox="0 0 124 124"><circle cx="62" cy="62" r="58" fill="none" stroke="#fff" stroke-width="3"/><circle cx="62" cy="62" r="48" fill="#fff"/><g fill="#0d3c8f"><circle cx="62" cy="50" r="8"/><path d="M48 78a14 14 0 0 1 28 0z"/><circle cx="44" cy="56" r="6"/><path d="M33 78a11 11 0 0 1 20-6v6z"/><circle cx="80" cy="56" r="6"/><path d="M91 78a11 11 0 0 0-20-6v6z"/></g></svg>
    <p>Sed ut perspiciatis unde omnis iste natus error sit voluptatem accusantium doloremque laudantium, totam rem aperiam, eaque ipsa quae ab illo inventore veritatis et quasi architecto beatae vitae dicta sunt explicabo.</p>
  </article>

  <article class="service-card" style="left:357px">
    <h3>Media Relations</h3>
    <svg width="118" height="118" viewBox="0 0 124 124"><circle cx="62" cy="62" r="58" fill="none" stroke="#e3001b" stroke-width="3"/><circle cx="62" cy="62" r="48" fill="#e3001b"/><g fill="none" stroke="#fff" stroke-width="3"><rect x="40" y="40" width="44" height="30"/></g><g fill="#fff"><circle cx="54" cy="74" r="5"/><circle cx="70" cy="74" r="5"/><rect x="48" y="80" width="12" height="10"/><rect x="64" y="80" width="12" height="10"/></g></svg>
    <p>Sed ut perspiciatis unde omnis iste natus error sit voluptatem accusantium doloremque laudantium, totam rem aperiam, eaque ipsa quae ab illo inventore veritatis et quasi architecto beatae vitae dicta sunt explicabo.</p>
  </article>

  <article class="service-card" style="left:626px">
    <h3>Public Affairs</h3>
    <svg width="118" height="118" viewBox="0 0 124 124"><circle cx="62" cy="62" r="58" fill="none" stroke="#e3001b" stroke-width="3"/><circle cx="62" cy="62" r="48" fill="#e3001b"/><circle cx="62" cy="62" r="22" fill="none" stroke="#fff" stroke-width="3"/><path d="M42 62h40M62 40v44" stroke="#fff" stroke-width="2"/><path d="M70 40l14 8-6 4z" fill="#fff"/></svg>
    <p>Sed ut perspiciatis unde omnis iste natus error sit voluptatem accusantium doloremque laudantium, totam rem aperiam, eaque ipsa quae ab illo inventore veritatis et quasi architecto beatae vitae dicta sunt explicabo.</p>
  </article>

  <article class="service-card" style="left:896px">
    <h3>Marketing Communication</h3>
    <svg width="118" height="118" viewBox="0 0 124 124"><circle cx="62" cy="62" r="58" fill="none" stroke="#e3001b" stroke-width="3"/><circle cx="62" cy="62" r="48" fill="#e3001b"/><path d="M36 58l14-10 12 8 12-8 14 10-14 14-12-6-12 6z" fill="none" stroke="#fff" stroke-width="3" stroke-linejoin="round"/></svg>
    <p>Sed ut perspiciatis unde omnis iste natus error sit voluptatem accusantium doloremque laudantium, totam rem aperiam, eaque ipsa quae ab illo inventore veritatis et quasi architecto beatae vitae dicta sunt explicabo.</p>
  </article>
</section>

<section class="cta">
  <h2>Are you ready to start a conversation?</h2>
  <a class="btn">Get in Touch</a>
</section>

<section class="agency" role="img" aria-label="Black and white photo of a broadcast camera crew at work">
  <h2>We are public relations agency specializing in media relations</h2>
  <p>At vero eos et accusamus et iusto odio dignissimos ducimus qui blanditiis praesentium voluptatum deleniti atque corrupti quos dolores.</p>
</section>

<section class="team">
  <h2 class="section-title">Our Team</h2>
  <p class="lede">Professional &amp; outstanding ideas of our passionate team makes us unique in every sense.</p>
  <div class="member" style="left:86px;background:radial-gradient(circle at 50% 40%,#d8c8b8,#6a6a6a)" role="img" aria-label="Portrait photo of a team member"></div>
  <div class="member" style="left:368px;background:radial-gradient(circle at 50% 40%,#cdb49a,#8a7a66)" role="img" aria-label="Portrait photo of a team member"></div>
  <div class="member" style="left:642px;background:radial-gradient(circle at 50% 40%,#c89a80,#3f6e8a)" role="img" aria-label="Portrait photo of a team member"></div>
  <div class="member" style="left:908px;background:radial-gradient(circle at 50% 40%,#4a4a4a,#2a2a2a)" role="img" aria-label="Portrait photo of team member Dale Winters"><span class="member-name">Dale Winters</span></div>
</section>

<section class="testimonials" role="img" aria-label="Black and white photo of people walking in an office lobby">
  <h2>Testimonilas</h2>
  <svg class="quote-mark" width="32" height="28" viewBox="0 0 32 28"><path d="M0 28V16C0 6 5 1 13 0v5c-4 1-6 4-6 9h6v14zM19 28V16c0-10 5-15 13-16v5c-4 1-6 4-6 9h6v14z" fill="#fff"/></svg>
  <p>Sed ut perspiciatis unde omnis iste natus error sit voluptatem accusantium doloremque laudantium, totam rem aperiam, eaque ipsa quae ab illo inventore veritatis et quasi architecto beatae vitae dicta sunt explicabo. Nemo enim ipsam voluptatem quia voluptas sit aspernatur aut odit aut fugit.</p>
  <cite>Nora Pell, Halvern Defense Systems</cite>
</section>

<section class="clients">
  <h2 class="section-title">We've managed events for clients including:</h2>
  <div class="client-row">
    <span>Ridewell</span><span>Northfield Fund</span><span>Gearhaus</span><span>Osprey Bay</span><span>Lakeside ER</span><span>Ashcombe</span><span>Clearmind</span><span>Midstate</span><span>TRELVOX</span><span>QCU</span>
  </div>
</section>

<section class="news">
  <h2 class="section-title">Latest News</h2>
  <div class="news-arrows">
    <svg width="12" height="16" viewBox="0 0 12 16"><path d="M9 2L3 8l6 6" fill="none" stroke="#111" stroke-width="2.5"/></svg>
    <svg width="12" height="16" viewBox="0 0 12 16"><path d="M3 2l6 6-6 6" fill="none" stroke="#111" stroke-width="2.5"/></svg>
  </div>
  <div class="news-tile" style="left:0;background:linear-gradient(135deg,#6a6a6a,#1e1e1e)" role="img" aria-label="Photo of a hand using a tablet with floating media icons"></div>
  <article class="news-tile news-card" style="left:304px">
    <h3>Lorem Ipsum Dolor</h3>
    <time>30 Aug 2014</time>
    <p>Sed ut perspiciatis unde omnis iste natus error sit voluptatem accusantium eaque ipsa quae ab illo inventore veritatis et quasi architecto beatae vitae dicta sunt explicabo</p>
  </article>
  <div class="news-tile" style="left:606px;background:linear-gradient(135deg,#d8d8d8,#7a7a7a)" role="img" aria-label="Photo of hands typing on a laptop keyboard"></div>
  <div class="news-tile" style="left:908px;background:linear-gradient(135deg,#9a9a9a,#3a3a3a)" role="img" aria-label="Photo of a person working at a laptop"></div>
</section>

<section class="contact">
  <h2>Contact Us</h2>
  <div class="field" style="left:86px;top:83px;width:256px;height:61px">Name</div>
  <div class="field" style="left:350px;top:83px;width:256px;height:61px">Mail</div>
  <div class="field" style="left:86px;top:154px;width:520px;height:141px">Message</div>
  <div class="submit">Submit</div>

  <div class="info" style="top:88px">
    <svg width="16" height="20" viewBox="0 0 16 20"><path d="M8 0a8 8 0 0 0-8 8c0 6 8 12 8 12s8-6 8-12a8 8 0 0 0-8-8zm0 11a3 3 0 1 1 0-6 3 3 0 0 1 0 6z" fill="#fff"/></svg>
    <span>Sed ut perspiciatis unde omnis iste natus error sit voluptatem accusantium doloremque laudantium.</span>
  </div>
  <div class="info" style="top:144px">
    <svg width="16" height="12" viewBox="0 0 16 12"><rect width="16" height="12" fill="#fff"/><path d="M0 0l8 6 8-6" fill="none" stroke="#e3001b" stroke-width="1.5"/></svg>
    <span>Marisol@TRELVOXstudio.example</span>
  </div>
  <div class="info" style="top:186px">
    <svg width="16" height="16" viewBox="0 0 16 16"><path d="M3 0l3 4-2 2c1 2 4 5 6 6l2-2 4 3-2 3C7 16 0 9 0 3z" fill="#fff"/></svg>
    <span>(407) 555-0164</span>
  </div>
</section>

<footer class="site-footer">©2014 trelvoxstudio.example. All rights reserved.</footer>

</body>
</html>
```